project - Misto Den

Dear designers, I'm Looking for an appealing new business card design to represent us for our new e-cigarette store: The MistO Den. Knowledgeable and friendly staff we aim for superior customer service with a positive atmosphere. Classic feel with modern touch is what we are aiming for . Lime green font and grey back round is the original color scheme but we are flexible and open to suggestions. I added some doodles to show you where my mind is at. address: 4827 203 St SW Edmonton, AB (inside the grand swap bazaar)web: themistoden.com email: info@themistoden.com phone : 555.214.6093 Thanks and am looking forward to seeing your creative , fresh and innovative designs.
Good luck everybody!
Gordon
Updates
lime green and charcoal grey please. thanks
Industry/Entity Type
Business
Logo Text
The MistO Den
Look and feel
Each slider illustrates characteristics of the customer's brand and the style your logo design should communicate.

```html
<!DOCTYPE html>
<html lang="en">
<head>
<meta charset="utf-8">
<title>The MistO Den — Business Card</title>
<link href="https://fonts.googleapis.com/css2?family=Cabin:wght@500&display=swap" rel="stylesheet">
<style>
  :root {
    --page: #ffffff;
    --charcoal: #252c2d;
    --charcoal-faint: #2f3839;
    --lime: #b9f20d;
    --grey: #808080;
    --icon-grey: #9a9a9a;
  }
  html, body {
    margin: 0;
    width: 1200px;
    height: 1000px;
    overflow: hidden;
    background: var(--page);
  }
  .card {
    position: absolute;
    left: 57px;
    top: 181px;
    width: 1086px;
    height: 637px;
    background: var(--charcoal);
    font-family: "Cabin", sans-serif;
    overflow: hidden;
  }
  .brand-mark {
    position: absolute;
    left: 216px;
    top: 360px;
    width: 90px;
    height: 90px;
  }
  .brand-watermark {
    position: absolute;
    left: 433px;
    top: 166px;
    margin: 0;
    font-size: 100px;
    font-weight: 500;
    line-height: 1;
    color: var(--charcoal-faint);
    white-space: nowrap;
  }
  .contact-rule {
    position: absolute;
  }
  .contact-rule--lime {
    left: 538px;
    top: 384px;
    width: 3px;
    height: 208px;
    background: var(--lime);
  }
  .contact-rule--grey {
    left: 544px;
    top: 369px;
    width: 3px;
    height: 208px;
    background: var(--grey);
  }
  .contact {
    position: absolute;
    left: 569px;
    top: 376px;
    margin: 0;
    padding: 0;
    list-style: none;
    color: var(--lime);
    font-size: 28px;
    font-weight: 500;
    line-height: 38px;
  }
  .contact__row {
    display: flex;
    align-items: center;
    height: 40px;
  }
  .contact__row--address { height: 38px; }
  .contact__icon {
    width: 38px;
    height: 30px;
    margin-right: 8px;
    flex: none;
  }
  .footer-band {
    position: absolute;
    left: 0;
    bottom: 0;
    height: 34px;
  }
  .footer-band--lime { width: 198px; background: var(--lime); }
  .footer-band--grey { left: 202px; right: 0; background: var(--grey); }
</style>
</head>
<body>
  <section class="card">
    <svg class="brand-mark" viewBox="0 0 90 90" aria-hidden="true">
      <circle cx="45" cy="45" r="36" fill="none" stroke="var(--icon-grey)" stroke-width="6"/>
    </svg>

    <p class="brand-watermark">The MistO Den</p>

    <div class="contact-rule contact-rule--grey"></div>
    <div class="contact-rule contact-rule--lime"></div>

    <ul class="contact">
      <li class="contact__row contact__row--address">4827 203 St SW Edmonton</li>
      <li class="contact__row contact__row--address">AB (inside the grand swap bazaar)</li>
      <li class="contact__row">
        <svg class="contact__icon" viewBox="0 0 38 30" aria-hidden="true">
          <g fill="none" stroke="var(--icon-grey)" stroke-width="1.6">
            <circle cx="19" cy="15" r="13"/>
            <ellipse cx="19" cy="15" rx="6" ry="13"/>
            <line x1="6" y1="10" x2="32" y2="10"/>
            <line x1="6" y1="20" x2="32" y2="20"/>
          </g>
          <rect x="8" y="12" width="22" height="7" fill="var(--charcoal)"/>
          <text x="19" y="18.5" font-size="7" text-anchor="middle" fill="var(--icon-grey)" font-family="Cabin, sans-serif">www</text>
        </svg>
        <span>: themistoden.com</span>
      </li>
      <li class="contact__row">
        <svg class="contact__icon" viewBox="0 0 38 30" aria-hidden="true">
          <g fill="none" stroke="var(--icon-grey)" stroke-width="2">
            <rect x="3" y="5" width="32" height="21"/>
            <polyline points="3,5 19,17 35,5"/>
            <line x1="3" y1="26" x2="15" y2="14"/>
            <line x1="35" y1="26" x2="23" y2="14"/>
          </g>
        </svg>
        <span>: info@themistoden.com</span>
      </li>
      <li class="contact__row">
        <svg class="contact__icon" viewBox="0 0 38 30" aria-hidden="true">
          <path d="M12 2 L17 2 L18 9 L15 11 C15 16 17 20 20 23 L23 21 L28 25 L26 29 C16 28 9 18 10 6 Z" fill="var(--icon-grey)"/>
        </svg>
        <span>: 555.214.6093</span>
      </li>
    </ul>

    <div class="footer-band footer-band--lime"></div>
    <div class="footer-band footer-band--grey"></div>
  </section>
</body>
</html>
```